Corvane Paintless Dent Removal

Our company works on vehicles removing dents using a highly skilled trade which the metal is massaged out with special tools without disturbing the original paint, hence paintless dent removal. Besides keeping the paint and metal original its also very environmentally friendly since no paint or toxic fillers are used. Also we we are one of the most experienced companies in the business with 25 years

Target Market(s)

Retail Automobile consumers, Auto Dealerships and Auto Body Shops

Industry/Entity Type

Auto Repair

Contact Information for Business Card

Dale Hollister
PO Box 518 Brookmere, NY 11962
631-555-0148
corvanepdr@mailbox-example.com
website corvanepdr.example
youtube corvane paintless dent removal
25 years of experience removing Dents, Dings and Hail Damage

Font styles to use
Serif
Sans Serif

Colors

Designer to choose colors to be used in the design.

Requirements
Must have
• I do like things that are simple but classy and somewhat bold, also I like my logo so that should be somewhat important

```html
<!DOCTYPE html>
<html lang="en">
<head>
<meta charset="utf-8">
<title>Corvane Paintless Dent Removal – Business Card</title>
<link rel="stylesheet" href="https://fonts.googleapis.com/css2?family=Arimo:wght@400;700&display=swap">
<style>
  :root {
    --navy: #0f2a4e;
    --green: #76c41c;
    --card: #fbfaf8;
    --backdrop: #e9e7e4;
    --white: #ffffff;
  }
  * { margin: 0; padding: 0; box-sizing: border-box; }
  html, body {
    width: 1200px; height: 900px; overflow: hidden;
    background: var(--backdrop);
    font-family: "Arimo", Arial, sans-serif;
  }
  .business-card {
    position: absolute; left: 120px; top: 152px;
    width: 960px; height: 595px;
    background: var(--card);
    box-shadow: 0 10px 30px rgba(0,0,0,0.15);
    overflow: hidden;
  }
  .card-band { position: absolute; inset: 0; width: 960px; height: 595px; }
  .brand {
    position: absolute; left: 56px; top: 92px;
    display: flex; align-items: center; gap: 16px;
  }
  .brand-dot { width: 26px; height: 26px; border-radius: 50%; background: var(--green); }
  .brand-name {
    font-weight: 700; color: var(--navy);
    font-size: 30px; line-height: 1.15; letter-spacing: 0.5px;
  }
  .holder-name {
    position: absolute; right: 38px; top: 70px;
    font-weight: 700; font-size: 33px; letter-spacing: 0.5px;
    color: var(--navy); text-transform: uppercase;
  }
  .holder-name .surname { color: var(--green); }
  .tagline {
    position: absolute; left: 54px; top: 273px;
    font-size: 23px; line-height: 30px; color: var(--navy);
    text-transform: uppercase; letter-spacing: 0.3px;
  }
  .contact {
    position: absolute; right: 48px; top: 318px;
    color: var(--white); font-size: 25px; text-align: right;
    list-style: none;
  }
  .contact li { display: flex; justify-content: flex-end; align-items: center; gap: 8px; height: 35px; }
  .contact .address { height: 35px; }
  .contact .phone { margin-top: 12px; }
  .contact .channel { margin-top: 18px; }
  .contact svg { width: 18px; height: 18px; flex: none; }
  .icon-square { width: 17px; height: 17px; background: var(--green); flex: none; }
</style>
</head>
<body>
  <article class="business-card">
    <svg class="card-band" viewBox="0 0 960 595" aria-hidden="true">
      <path d="M0,428 L300,428 C520,380 720,250 960,222 L960,595 L0,595 Z" fill="#76c41c"/>
      <path d="M0,442 L305,442 C525,394 725,264 960,236 L960,595 L0,595 Z" fill="#0f2a4e"/>
    </svg>

    <div class="brand">
      <span class="brand-dot"></span>
      <span class="brand-name">Corvane<br>Paintless Dent Removal</span>
    </div>

    <h1 class="holder-name">Dale <span class="surname">Hollister</span></h1>

    <p class="tagline">25 years of experience<br>removing dents, dings<br>and hail damage</p>

    <ul class="contact">
      <li class="address">PO Box 518 Brookmere</li>
      <li class="address">NY 11962</li>
      <li class="phone">631-555-0148
        <svg viewBox="0 0 20 20"><path fill="#76c41c" d="M5 2l3 4-2 2c1 2 3 4 5 5l2-2 4 3-2 3C9 17 3 11 2 4z"/></svg>
      </li>
      <li>corvanepdr@mailbox-example.com
        <svg viewBox="0 0 20 20"><rect x="2" y="4" width="16" height="12" fill="#76c41c"/><path d="M2 4l8 7 8-7" fill="none" stroke="#0f2a4e" stroke-width="1.6"/></svg>
      </li>
      <li>corvanepdr.example
        <svg viewBox="0 0 20 20"><circle cx="10" cy="10" r="8" fill="#76c41c"/></svg>
      </li>
      <li class="channel">corvane paintless dent removal <span class="icon-square"></span></li>
    </ul>
  </article>
</body>
</html>
```